Website design for a hair building fibre

Hi I’m needing a website made for both men and women to purchase the product is a hair building fibre that you apply to thinning hair to make your hair look really thick I’ll need the website to be easy to use professional and also very classy I will need it to work with lumen split tok fund and credit cards I’ll need to have the CEO words and everything ready so I can sell I don’t have photos that I want to put on there so I’ll need a website designer to assist me in having the beautiful photos on there I know very little about websites so I need someone to be able to do it all for me

I can only provide photos of the colours of the products
I believe there will be 8 colours to sell as well
I’ve uploaded a photo of the logo I’d really like it if the website designer can check other competitors website so my website does not look like theres, I don’t want my website to look like a copied website of the competitors I’m located in Australia.
I’m also looking for someone who can open up a Palvista and Glimmerly page and then can unload photos on them ready for consumers to view and buy.

```html
<!DOCTYPE html>
<html lang="en">
<head>
<meta charset="utf-8">
<title>Fibrelle — Hair Building Fibre</title>
<link href="https://fonts.googleapis.com/css2?family=Lato:wght@400;700&family=Raleway:wght@300;400;500;600&display=swap" rel="stylesheet">
<style>
:root{
  --accent:#6cc3e6;
  --accent-dark:#3fa9d4;
  --navy:#1a2332;
  --navy-deep:#121b27;
  --footer:#151d29;
  --ink:#222831;
  --muted:#4a5059;
  --light:#f3f4f6;
  --line:#dfe3e8;
  --star:#f2b01e;
}
*{box-sizing:border-box;margin:0;padding:0}
html,body{width:1200px;height:5268px;overflow:hidden}
body{font-family:"Lato",sans-serif;color:var(--ink);background:#fff;position:relative}
section,header,footer{position:relative;width:1200px;overflow:hidden}
.abs{position:absolute}
.section-title{position:absolute;left:0;width:1200px;text-align:center;font-family:"Raleway",sans-serif;font-weight:400;font-size:33px;letter-spacing:1px;text-transform:uppercase;color:var(--ink)}
.section-title::after{content:"";display:block;width:34px;height:3px;background:var(--accent);margin:18px auto 0}
.section-title.on-dark{color:#fff}

/* top bar */
.top-bar{height:28px;background:var(--accent);text-align:center;font-size:11px;font-weight:700;line-height:28px;color:var(--navy);letter-spacing:.2px}

/* hero */
.hero{height:632px;background:var(--navy)}
.hero-photo{position:absolute;right:0;top:0;width:640px;height:632px;background:radial-gradient(ellipse at 55% 45%,#8a5a3a 0%,#5a3a26 30%,#2a2420 60%,var(--navy) 85%)}
.logo{position:absolute;left:86px;top:22px;color:#b9c4d2}
.logo .name{font-family:"Raleway",sans-serif;font-weight:300;font-size:34px;letter-spacing:1px;line-height:1}
.logo .tag{font-family:"Raleway",sans-serif;font-weight:300;font-size:11px;letter-spacing:2.6px;margin-top:4px}
.main-nav{position:absolute;left:318px;top:60px;display:flex;gap:34px;font-size:12px;font-weight:700;color:#fff}
.main-nav a{color:#fff;text-decoration:none;position:relative}
.main-nav a.active{color:var(--accent)}
.main-nav a.active::after{content:"";position:absolute;left:50%;top:20px;width:6px;height:6px;margin-left:-3px;background:#fff;border-radius:50%}
.header-icons{position:absolute;left:908px;top:52px;display:flex;gap:10px}
.header-icons span{width:36px;height:36px;border-radius:50%;background:#fff;display:flex;align-items:center;justify-content:center}
.cart{position:absolute;left:1054px;top:52px;color:#fff}
.cart .lbl{font-size:10px;font-weight:700}
.cart .amt{font-family:"Raleway",sans-serif;font-size:25px;color:var(--accent);line-height:1}
.hero-copy{position:absolute;left:78px;top:196px;width:540px;color:#fff}
.hero-copy .kicker{font-family:"Raleway",sans-serif;font-size:21px;letter-spacing:.5px}
.hero-copy h1{font-family:"Raleway",sans-serif;font-weight:400;font-size:47px;color:var(--accent);letter-spacing:1px;margin-top:14px}
.hero-copy p{font-size:12.5px;line-height:28px;margin-top:14px;color:#e8ecf1}
.btn{display:inline-block;background:var(--accent);color:var(--navy);font-weight:700;font-size:14px;border-radius:24px;padding:13px 20px;letter-spacing:.3px}
.hero-copy .btn{margin-top:28px}
.slider-dots{position:absolute;left:0;width:100%;display:flex;justify-content:center;gap:6px}
.slider-dots i{width:8px;height:8px;border-radius:50%;background:#fff;display:block}
.slider-dots i.on{background:var(--accent)}

/* products */
.products{height:726px}
.products.best{height:754px}
.product-card{position:absolute;width:284px;text-align:center}
.product-card .frame{height:315px;border:2px solid var(--line);border-radius:10px;background:#fff;display:flex;align-items:center;justify-content:center}
.product-card.selected .frame{border-color:#9fd3ea}
.product-shot{width:90px;height:260px;border-radius:8px;background:linear-gradient(180deg,#1a1a1a 0%,#2b2b2b 22%,#cfd2d5 24%,#eceef0 50%,#b3b7bb 76%,#8e9296 100%)}
.swatches{display:flex;justify-content:center;align-items:center;gap:6px;margin-top:18px}
.swatches i{width:33px;height:33px;border-radius:50%;display:block}
.swatches b{font-weight:400;font-size:14px;margin-left:6px}
.product-card .name{font-size:16px;line-height:28px;margin-top:10px}
.stars{color:var(--star);font-size:12px;letter-spacing:1px;margin-top:2px}
.price{color:var(--accent);font-size:16px;margin-top:2px}
.arrow{position:absolute;width:24px;height:38px}

/* deal */
.deal{height:488px;background:var(--navy-deep)}
.deal-card{position:absolute;top:155px;width:454px;height:260px;border-radius:8px;overflow:hidden;background:linear-gradient(90deg,#254a66,#2f6d8f 60%,#3b85ad)}
.deal-photo{position:absolute;top:0;width:200px;height:260px}
.deal-card .offer{position:absolute;width:240px;text-align:center;color:#fff;top:14px}
.deal-card .pct{font-family:"Raleway",sans-serif;font-size:56px;font-weight:300;line-height:1.1}
.deal-card .off{font-family:"Raleway",sans-serif;font-size:21px;letter-spacing:2px}
.deal-card p{font-size:11.5px;line-height:24px;margin:12px 18px 0}
.deal-card .btn{font-size:12px;padding:11px 18px;margin-top:14px;color:#fff;background:var(--accent-dark)}

/* features */
.features{height:540px;background:var(--light)}
.feature{position:absolute;top:186px;width:230px;text-align:center}
.feature .ico{width:134px;height:134px;border-radius:50%;background:#d8ecf6;margin:0 auto;display:flex;align-items:center;justify-content:center}
.feature .ico.on{background:var(--accent)}
.feature h3{font-size:15px;font-weight:700;margin-top:34px;letter-spacing:.3px}
.feature p{font-size:12.3px;line-height:28px;color:var(--muted);margin-top:6px}

/* video */
.video{height:526px;background:linear-gradient(180deg,#6a717a 0%,#4a4f56 40%,#2a2b2e 75%,#55595f 100%)}
.play{position:absolute;left:561px;top:226px;width:76px;height:76px;border-radius:50%;background:rgba(108,195,230,.35);display:flex;align-items:center;justify-content:center}

/* before after */
.before-after{height:613px}
.ba-card{position:absolute;top:192px;width:456px;height:312px;border:3px solid #eef0f2;box-shadow:0 0 6px rgba(0,0,0,.12);display:flex}
.ba-card div{flex:1}

/* testimonials */
.testimonials{height:603px;background:var(--light)}
.avatar{position:absolute;border-radius:50%;background:linear-gradient(160deg,#c9ccd1,#6d737b)}
.quote-name{position:absolute;top:296px;width:100%;text-align:center;color:var(--accent);font-size:16px;letter-spacing:1px}
.quote{position:absolute;top:330px;left:290px;width:620px;text-align:center;font-size:18px;line-height:32px;font-weight:700;color:#2b3038;font-family:"Raleway",sans-serif}
.t-dots{top:497px}
.t-dots i{background:#c8d8e6;width:11px;height:11px}

/* footer */
.site-footer{height:358px;background:var(--footer);color:#fff}
.fcol{position:absolute;top:74px}
.fcol h4{font-size:14px;font-weight:700;letter-spacing:.5px;margin-bottom:14px}
.fcol li{list-style:none;font-size:11.5px;line-height:28px}
.fcol li::before{content:"»";margin-right:8px}
.contact li::before{content:none}
.contact li{display:flex;gap:12px;line-height:24px;margin-bottom:12px}
.footer-logo{position:absolute;left:818px;top:88px;color:#b9c4d2}
.footer-logo .name{font-family:"Raleway",sans-serif;font-weight:300;font-size:46px;line-height:1}
.footer-logo .tag{font-family:"Raleway",sans-serif;font-weight:300;font-size:15px;letter-spacing:3.3px;margin-top:6px}
.socials{position:absolute;left:852px;top:186px;display:flex;gap:14px}
.socials span{width:30px;height:30px;border-radius:50%;background:var(--accent-dark);color:#fff;font-size:13px;font-weight:700;display:flex;align-items:center;justify-content:center}
.copyright{position:absolute;top:286px;width:100%;text-align:center;font-size:11px}
.payments{position:absolute;top:310px;width:100%;display:flex;justify-content:center;gap:4px}
.payments span{height:16px;border-radius:2px;background:#e9edf1;color:var(--navy);font-size:8px;font-weight:700;line-height:16px;padding:0 4px}
.payments span.card{width:24px;padding:0}
</style>
</head>
<body>

<div class="top-bar">LOREM IPSUM DOLOR SIT AMET, CONSECTETUR ADIPISCING ELIT, SED DO</div>

<header class="hero">
  <div class="hero-photo" role="img" aria-label="Portrait of a woman with full, voluminous curly hair"></div>
  <div class="logo"><div class="name">Fibrelle</div><div class="tag">HAIR BUILDING FIBRE</div></div>
  <nav class="main-nav">
    <a class="active">HOME</a><a>OUR SHOP</a><a>REVIEWS</a><a>BLOG</a><a>HOW IT WORKS</a><a>CONTACT US</a>
  </nav>
  <div class="header-icons">
    <span><svg width="16" height="16" viewBox="0 0 16 16"><circle cx="8" cy="5" r="3" fill="none" stroke="#1a2332" stroke-width="1.6"/><path d="M2 15c0-3.5 2.7-5 6-5s6 1.5 6 5" fill="none" stroke="#1a2332" stroke-width="1.6"/></svg></span>
    <span><svg width="16" height="16" viewBox="0 0 16 16"><path d="M8 14 2 8a3.3 3.3 0 0 1 6-4 3.3 3.3 0 0 1 6 4z" fill="#1a2332"/></svg></span>
    <span><svg width="16" height="16" viewBox="0 0 16 16"><path d="M1 2h2.5l2 8h7.5l1.5-6H5" fill="none" stroke="#1a2332" stroke-width="1.6"/><circle cx="6.5" cy="13.5" r="1.3" fill="#1a2332"/><circle cx="12" cy="13.5" r="1.3" fill="#1a2332"/></svg></span>
  </div>
  <div class="cart"><div class="lbl">MY CART</div><div class="amt">00.00</div></div>
  <div class="hero-copy">
    <div class="kicker">WELCOME TO FIBRELLE</div>
    <h1>HAIR BUILDING FIBRE</h1>
    <p>Lorem ipsum dolor sit amet, consectetur adipiscing elit, sed do eiusmod tempor incididunt ut labore et dolore magna aliqua. Quis ipsum suspendisse ultrices gravida. Risus commodo viverra maecenas accumsan lacus vel facilisis.</p>
    <span class="btn">SHOP OUR PRODUCTS</span>
  </div>
  <div class="slider-dots" style="top:592px"><i></i><i class="on"></i><i></i><i></i></div>
</header>

<section class="products">
  <h2 class="section-title" style="top:732px;top:72px">Our Featured Products</h2>
  <svg class="arrow" style="left:46px;top:350px" viewBox="0 0 24 38"><path d="M18 3 4 19l14 16" fill="none" stroke="#333" stroke-width="2"/></svg>
  <svg class="arrow" style="left:1130px;top:350px" viewBox="0 0 24 38"><path d="M6 3l14 16L6 35" fill="none" stroke="#333" stroke-width="2"/></svg>

  <div class="product-card" style="left:131px;top:180px">
    <div class="frame"><div class="product-shot" role="img" aria-label="Hair building fibre canister"></div></div>
    <div class="swatches"><i style="background:#2a1a10"></i><i style="background:#8b7a52"></i><i style="background:#2f3a35"></i><i style="background:#7f8b72"></i><i style="background:#4a1a0e"></i><b>(3)</b></div>
    <div class="name">Lorem ipsum dolor sit amet<br>consectetur adip.</div>
    <div class="stars">★★★★★</div><div class="price">$ 250:00</div>
  </div>
  <div class="product-card selected" style="left:458px;top:180px">
    <div class="frame"><div class="product-shot" role="img" aria-label="Hair building fibre canister"></div></div>
    <div class="swatches"><i style="background:#2a1a10"></i><i style="background:#8b7a52"></i><i style="background:#2f3a35"></i><i style="background:#7f8b72"></i><i style="background:#4a1a0e"></i><b>(3)</b></div>
    <div class="name">Lorem ipsum dolor sit amet<br>consectetur adip.</div>
    <div class="stars">★★★★★</div><div class="price">$ 250:00</div>
  </div>
  <div class="product-card" style="left:785px;top:180px">
    <div class="frame"><div class="product-shot" role="img" aria-label="Hair building fibre canister"></div></div>
    <div class="swatches"><i style="background:#2a1a10"></i><i style="background:#8b7a52"></i><i style="background:#2f3a35"></i><i style="background:#7f8b72"></i><i style="background:#4a1a0e"></i><b>(3)</b></div>
    <div class="name">Lorem ipsum dolor sit amet<br>consectetur adip.</div>
    <div class="stars">★★★★★</div><div class="price">$ 250:00</div>
  </div>
</section>

<section class="deal">
  <h2 class="section-title on-dark" style="top:68px">Deal of the Week</h2>
  <div class="deal-card" style="left:133px">
    <div class="deal-photo" role="img" aria-label="Man with thick styled hair" style="left:0;background:linear-gradient(90deg,#1e3a52,#3b3a3c 50%,#2c5a78)"></div>
    <div class="offer" style="left:214px">
      <div class="pct">50%</div><div class="off">OFFERS</div>
      <p>Lorem ipsum dolor sit amet, cons ectetur adipiscing elit, sed do eiu smod tempor incididunt.</p>
      <span class="btn">PRODUCT FOR MEN</span>
    </div>
  </div>
  <div class="deal-card" style="left:613px">
    <div class="deal-photo" role="img" aria-label="Woman with long wavy dark hair" style="right:0;background:linear-gradient(90deg,#3b85ad,#2a2a30 50%,#4a7fa3)"></div>
    <div class="offer" style="left:0">
      <div class="pct">50%</div><div class="off">OFFERS</div>
      <p>Lorem ipsum dolor sit amet, cons ectetur adipiscing elit, sed do eiu smod tempor incididunt.</p>
      <span class="btn">PRODUCT FOR WOMEN</span>
    </div>
  </div>
</section>

<section class="features">
  <h2 class="section-title" style="top:98px">Full Hair, Instantly</h2>
  <div class="feature" style="left:104px">
    <div class="ico"><svg width="60" height="70" viewBox="0 0 60 70" fill="none" stroke="#1a2332" stroke-width="2.4"><path d="M24 4h14v10H24zM20 14h22v8H20zM14 22h32a4 4 0 0 1 4 4v36a4 4 0 0 1-4 4H14a4 4 0 0 1-4-4V26a4 4 0 0 1 4-4z"/><path d="M30 36c-4 6-6 9-6 12a6 6 0 0 0 12 0c0-3-2-6-6-12z"/></svg></div>
    <h3>01 . EASY TO APPLY</h3>
    <p>Lorem ipsum dolor sit amet, consectetur adipiscing elit, sed do eiusmod tempor incididunt.</p>
  </div>
  <div class="feature" style="left:357px">
    <div class="ico on"><svg width="70" height="64" viewBox="0 0 70 64" fill="none" stroke="#fff" stroke-width="2.4"><path d="M18 6c-5 7-8 11-8 15a8 8 0 0 0 16 0c0-4-3-8-8-15zM50 6c-5 7-8 11-8 15a8 8 0 0 0 16 0c0-4-3-8-8-15zM35 22c-5 7-8 11-8 15a8 8 0 0 0 16 0c0-4-3-8-8-15z"/><path d="M6 54h58M12 48l4 6M24 48l4 6M36 48l4 6M48 48l4 6"/></svg></div>
    <h3>02 . RESISTANCE</h3>
    <p>Lorem ipsum dolor sit amet, consectetur adipiscing elit, sed do eiusmod tempor incididunt.</p>
  </div>
  <div class="feature" style="left:611px">
    <div class="ico"><svg width="64" height="64" viewBox="0 0 64 64" fill="none" stroke="#1a2332" stroke-width="2.4"><rect x="14" y="30" width="36" height="28" rx="3"/><path d="M14 40h36M32 30v28"/><path d="M22 22l20-14 6 8-20 14z"/></svg></div>
    <h3>03 . EASY REMOVAL</h3>
    <p>Lorem ipsum dolor sit amet, consectetur adipiscing elit, sed do eiusmod tempor incididunt.</p>
  </div>
  <div class="feature" style="left:866px">
    <div class="ico"><svg width="64" height="64" viewBox="0 0 64 64" fill="none" stroke="#1a2332" stroke-width="2.4"><circle cx="32" cy="32" r="24"/><path d="M21 33l8 8 15-17"/></svg></div>
    <h3>04 . RESULT ORIENTED</h3>
    <p>Lorem ipsum dolor sit amet, consectetur adipiscing elit, sed do eiusmod tempor incididunt.</p>
  </div>
</section>

<section class="products best">
  <h2 class="section-title" style="top:78px">Our Best Sellers</h2>
  <svg class="arrow" style="left:46px;top:376px" viewBox="0 0 24 38"><path d="M18 3 4 19l14 16" fill="none" stroke="#333" stroke-width="2"/></svg>
  <svg class="arrow" style="left:1130px;top:376px" viewBox="0 0 24 38"><path d="M6 3l14 16L6 35" fill="none" stroke="#333" stroke-width="2"/></svg>
  <div class="product-card" style="left:131px;top:186px">
    <div class="frame"><div class="product-shot" role="img" aria-label="Hair building fibre canister"></div></div>
    <div class="swatches"><i style="background:#2a1a10"></i><i style="background:#8b7a52"></i><i style="background:#2f3a35"></i><i style="background:#7f8b72"></i><i style="background:#4a1a0e"></i><b>(3)</b></div>
    <div class="name">Lorem ipsum dolor sit amet<br>consectetur adip.</div>
    <div class="stars">★★★★★</div><div class="price">$ 250:00</div>
  </div>
  <div class="product-card selected" style="left:458px;top:186px">
    <div class="frame"><div class="product-shot" role="img" aria-label="Hair building fibre canister"></div></div>
    <div class="swatches"><i style="background:#2a1a10"></i><i style="background:#8b7a52"></i><i style="background:#2f3a35"></i><i style="background:#7f8b72"></i><i style="background:#4a1a0e"></i><b>(3)</b></div>
    <div class="name">Lorem ipsum dolor sit amet<br>consectetur adip.</div>
    <div class="stars">★★★★★</div><div class="price">$ 250:00</div>
  </div>
  <div class="product-card" style="left:785px;top:186px">
    <div class="frame"><div class="product-shot" role="img" aria-label="Hair building fibre canister"></div></div>
    <div class="swatches"><i style="background:#2a1a10"></i><i style="background:#8b7a52"></i><i style="background:#2f3a35"></i><i style="background:#7f8b72"></i><i style="background:#4a1a0e"></i><b>(3)</b></div>
    <div class="name">Lorem ipsum dolor sit amet<br>consectetur adip.</div>
    <div class="stars">★★★★★</div><div class="price">$ 250:00</div>
  </div>
</section>

<section class="video" role="img" aria-label="Video still of a hand parting thinning hair on the crown of a man's head">
  <div class="play"><svg width="56" height="56" viewBox="0 0 56 56"><circle cx="28" cy="28" r="24" fill="none" stroke="#6cc3e6" stroke-width="4"/><path d="M23 18v20l16-10z" fill="none" stroke="#6cc3e6" stroke-width="3" stroke-linejoin="round"/></svg></div>
</section>

<section class="before-after">
  <h2 class="section-title" style="top:94px">Before &amp; After</h2>
  <svg class="arrow" style="left:76px;top:345px" viewBox="0 0 24 38"><path d="M18 3 4 19l14 16" fill="none" stroke="#333" stroke-width="2"/></svg>
  <svg class="arrow" style="left:1100px;top:345px" viewBox="0 0 24 38"><path d="M6 3l14 16L6 35" fill="none" stroke="#333" stroke-width="2"/></svg>
  <div class="ba-card" style="left:133px">
    <div role="img" aria-label="Before: thinning parting on a woman's auburn hair" style="background:linear-gradient(160deg,#b98a6c,#8a5a40 60%,#c9a58c)"></div>
    <div role="img" aria-label="After: fuller parting on a woman's auburn hair" style="background:linear-gradient(160deg,#a8785a,#7a4a30 60%,#c29c82)"></div>
  </div>
  <div class="ba-card" style="left:609px">
    <div role="img" aria-label="Before: thinning crown on a man's dark hair" style="background:linear-gradient(180deg,#e8eaec,#3a3230 45%,#d8b08a 85%)"></div>
    <div role="img" aria-label="After: fuller crown on a man's dark hair" style="background:linear-gradient(180deg,#e8eaec,#241e1c 45%,#d8b08a 85%)"></div>
  </div>
</section>

<section class="testimonials">
  <h2 class="section-title" style="top:98px">What Our Customers Say</h2>
  <div class="avatar" role="img" aria-label="Customer portrait" style="left:437px;top:190px;width:70px;height:70px"></div>
  <div class="avatar" role="img" aria-label="Customer portrait, Marisol" style="left:548px;top:174px;width:102px;height:102px"></div>
  <div class="avatar" role="img" aria-label="Customer portrait" style="left:687px;top:190px;width:70px;height:70px"></div>
  <div class="quote-name">MARISOL</div>
  <p class="quote">“Lorem ipsum dolor sit ameapttent taciti sociosqu ad litora torquent perinceptos himenaeos. Mauris in erat justo. Nullam ac urna eu felis dapibus condimentum sit amet a augue. Etiam pharetra, erat sed fermentum feugiat quis neque.”</p>
  <div class="slider-dots t-dots"><i></i><i></i><i></i><i class="on" style="background:var(--accent)"></i><i></i><i></i></div>
</section>

<footer class="site-footer">
  <div class="fcol" style="left:147px"><h4>QUICK LINKS</h4><ul><li>Home</li><li>Our Shop</li><li>Reviews</li><li>How it works</li><li>Contact Us</li></ul></div>
  <div class="fcol" style="left:366px"><h4>LEGAL</h4><ul><li>Terms of Use</li><li>Privacy Policy</li><li>Free Shipping</li><li>Blog</li><li>FAQ</li></ul></div>
  <div class="fcol contact" style="left:570px;width:220px"><h4>CONTACT US</h4><ul>
    <li><svg width="12" height="14" viewBox="0 0 12 14"><path d="M6 0a5 5 0 0 0-5 5c0 4 5 9 5 9s5-5 5-9a5 5 0 0 0-5-5z" fill="#fff"/><circle cx="6" cy="5" r="2" fill="#151d29"/></svg><span>123 Lorem ipsum dolor sit amet consectetur adipisci.</span></li>
    <li><svg width="12" height="14" viewBox="0 0 12 12"><path d="M2 0h2l1 3-1.5 1a7 7 0 0 0 4.5 4.5L9 7l3 1v2c0 1-1 2-2 2A10 10 0 0 1 0 2c0-1 1-2 2-2z" fill="#fff"/></svg><span>+61 2 5550 0134</span></li>
    <li><svg width="13" height="14" viewBox="0 0 13 10"><rect width="13" height="10" rx="1" fill="#fff"/><path d="M0 1l6.5 5L13 1" fill="none" stroke="#151d29" stroke-width="1.2"/></svg><span>hello@fibrelle.example</span></li>
  </ul></div>
  <div class="footer-logo"><div class="name">Fibrelle</div><div class="tag">HAIR BUILDING FIBRE</div></div>
  <div class="socials">
    <span aria-label="Palvista">P</span><span aria-label="Glimmerly">G</span><span aria-label="Chirpline">C</span><span aria-label="Netlace">N</span>
  </div>
  <div class="copyright">© copyrights 2022 Fibrelle &nbsp;|&nbsp;&nbsp; All rights reserved.</div>
  <div class="payments"><span class="card"></span><span class="card"></span><span>lumen split</span><span>tok fund</span></div>
</footer>

</body>
</html>
```